Dunfield Inc 1 pg brochure for entrepreneurs

We need a one page brochure (2 sided) designed for a finance and strategy consulting company called Dunfield Inc. which does work in Canada and the United States currently. This company works with entrepreneurs, helping them to establish finance operations, evaluate their financial infomation and apply insight from it to business strategies. Essentially we help entrepreneurs grow their business ... we take care of their finance needs and give them sound business advice ... allowing them to focus on their core business and business strategy.

This one page brochure is meant to caputure what services we provide but also positon that we are also entrepreneurs and we understand how entrepreneurs think .... we not only bring technical competence but cultural insight in this regard as well. We understand how nimble and stealth an entrepreneur's business is so we don't gouge them with expensive consulting fees. We don't want to look like a massive corporation ...we want to look professional, smart and reliable. We want to reflect that we are entrepreneural ourselves even in fact that we have a niche offering that is totally targeted to businesses of this nature.

Major emphasis points for the piece are
1) our core values, this could be a side bar or box
2) the credentials of our founder, he is technically competent and an entrepreneur himself (we have his picture to include)
3) our offerings, what we can do for a company, the client quotes provided are a good illustration of what we offer, the relief we provide a client and of what value we provide - make sure you read these, this could also be a side bar or box, some kind of special call out so the service offerings are very clear

The brochure needs to be editable, so in a format that we can work with it for future, if we need to make updates, one that we can use in Microsoft word and convert to a PDF format. It will be emailed to people (in pdf) and also brought to meetings.

We have a new logo and this design should be an extenstion of it from a colour, look and feel perspective. The piece should also be clean and not too copy heavy so we encourage use of sub-heads, whitespace, etc.

When we send this piece out or hand it to someone, the impression should be "I am comfortable with Dunfield Inc. they can help me and are people who get me, people I can trust to work closely with me on my business who are personally vested in my success".

Hello all, thank you for sumitting designs, there is some great work here.  A few changes/requests ...

Pls add the following headline on the front page right off the top

Entrepreneurs helping entrepreneurs, providing strategic financial services

Can we put Services on the front page? and call them out with treatment in a text box or with something strong that creates emphasis

Can the quote pls be broken up as opposed to one long list of 6 quotes? They can be floated throughout the piece, we can use less of them (or not) and put them on the front and back of the brochure? 

Also looking for the final product to be a little more bold in colour ...

Thx all, let us know if you have questions

Target Market(s)

Individuals (CEO) who runs their own established, yet growing business, who needs a business-minded CFO

Industry/Entity Type

Financial

Requirements
Must have
• Must have photo of founder, include his name and credentials under photo
All copy provide must be included
If not sure of a headline put in dummy text and we will provide headline or sub head copy
Should not have
• Fonts to be clean, no serif fonts. Should compliment logo, not the same font exactly but easily replicable in Microsoft Word and complimentary
No illustrations or cliche clip art

```html
<!DOCTYPE html>
<html lang="en">
<head>
<meta charset="utf-8">
<title>Dunfield Inc – Brochure</title>
<link rel="stylesheet" href="https://fonts.googleapis.com/css2?family=Arimo:ital,wght@0,400;0,700;1,400&display=swap">
<style>
  :root {
    --backdrop: #231f20;
    --paper: #ffffff;
    --navy: #2b2d6e;
    --navy-deep: #1c2466;
    --blue: #1a74c4;
    --cyan: #2fbfda;
    --panel-grey: #e4e4e6;
    --text: #3a3a3a;
    --text-soft: #555555;
    --photo-dark: #1b2230;
    --photo-blue: #1d5f9c;
  }
  * { box-sizing: border-box; margin: 0; padding: 0; }
  html, body { width: 1200px; height: 835px; overflow: hidden; }
  body {
    background: var(--backdrop);
    font-family: "Arimo", Arial, sans-serif;
    color: var(--text);
    position: relative;
  }
  .page {
    position: absolute;
    width: 538px;
    height: 696px;
    background: var(--paper);
  }
  .page--front { left: 49px; top: 73px; }
  .page--back { left: 613px; top: 74px; }
  .abs { position: absolute; }

  /* Brand */
  .brand-mark {
    left: 37px; top: 32px; width: 60px; height: 55px;
    border: 3px solid var(--blue);
  }
  .brand-mark::after {
    content: ""; position: absolute; left: 6px; top: 6px; right: 6px; bottom: 6px;
    background: var(--navy-deep);
  }
  .brand-name {
    left: 104px; top: 46px;
    font-size: 22px; font-weight: 400; color: var(--navy);
    letter-spacing: 0.5px;
  }
  .contact-rule { left: 281px; top: 31px; width: 1px; height: 54px; background: #777; }
  .contact {
    font-size: 10px; line-height: 14.5px; color: #333;
  }
  .contact--address { left: 292px; top: 39px; }
  .contact--lines { left: 400px; top: 39px; }
  .contact b { font-weight: 700; margin-right: 3px; }

  /* Hero */
  .hero-panel {
    left: 31px; top: 116px; width: 475px; height: 210px;
    border-radius: 14px 14px 0 0;
    background: linear-gradient(#e3e3e5, #ffffff 100%);
  }
  .headline {
    left: 51px; top: 133px;
    font-size: 37px; line-height: 45px; font-weight: 400; color: var(--navy);
  }
  .subhead {
    left: 51px; top: 225px;
    font-size: 23.5px; font-weight: 700; color: var(--navy);
  }
  .intro {
    left: 52px; top: 266px; width: 440px;
    font-size: 9.4px; line-height: 14px; color: var(--text-soft);
  }

  /* Section tabs */
  .tab {
    height: 22px; padding-left: 8px;
    font-size: 13.5px; line-height: 22px; color: #fff;
    background: var(--blue);
  }
  .tab::after {
    content: ""; position: absolute; right: 0; top: 0; width: 14px; height: 100%;
    background: var(--navy-deep);
    clip-path: polygon(100% 0, 100% 100%, 0 50%);
  }
  .tab--about { left: 52px; top: 331px; width: 121px; }
  .tab--services { left: 31px; top: 510px; width: 131px; }
  .tab--values { left: 339px; top: 78px; width: 135px; }
  .tab--testimonials { left: 43px; top: 516px; width: 120px; }

  .body-copy {
    font-size: 8.6px; line-height: 13px; color: var(--text-soft);
  }
  .body-copy p + p { margin-top: 13px; }
  .about-copy { left: 52px; top: 366px; width: 314px; }

  .photo-founder {
    left: 379px; top: 328px; width: 112px; height: 145px;
    background: linear-gradient(160deg, #3b3b3b, #161616 70%);
  }
  .caption { left: 379px; top: 483px; font-size: 8.4px; color: #222; }
  .caption small { display: block; font-size: 6px; margin-top: 3px; }

  /* Services */
  .services-panel {
    left: 31px; top: 518px; width: 475px; height: 126px;
    background: var(--cyan);
  }
  .bullet-list { list-style: none; color: #fff; }
  .bullet-list li { position: relative; padding-left: 13px; }
  .bullet-list li::before {
    content: ""; position: absolute; left: 0; top: 3px; width: 6px; height: 6px;
    background: var(--blue);
  }
  .services-list { font-size: 9.6px; line-height: 12.3px; }
  .services-list li + li { margin-top: 8px; }
  .services-list--left { left: 48px; top: 546px; width: 220px; }
  .services-list--right { left: 284px; top: 546px; width: 210px; }

  .site-url {
    right: 31px; top: 655px;
    font-size: 17px; color: var(--navy);
  }

  /* Back page */
  .back-panel {
    left: 32px; top: 49px; width: 473px; height: 594px;
    border-radius: 14px 14px 0 0;
    background: linear-gradient(#e3e3e5, #f7f7f8 30%, #ffffff 60%);
  }
  .photo-concept {
    left: 52px; top: 75px; width: 253px; height: 154px;
    background: linear-gradient(110deg, var(--photo-dark) 20%, var(--photo-blue) 75%, #3c8fcf);
  }
  .bio-copy { left: 55px; top: 237px; width: 265px; }
  .bio-copy p + p { margin-top: 13px; }

  .values-panel {
    left: 328px; top: 88px; width: 162px; height: 394px;
    background: var(--cyan);
  }
  .values-list { left: 342px; top: 120px; width: 144px; font-size: 9.4px; line-height: 12.3px; }
  .values-list li + li { margin-top: 11px; }

  .testimonials-panel {
    left: 32px; top: 529px; width: 473px; height: 112px;
    background: var(--panel-grey);
  }
  .quote {
    font-size: 7.8px; line-height: 12.2px; font-style: italic; color: #555;
  }
  .quote--one { left: 55px; top: 545px; width: 135px; }
  .quote--two { left: 214px; top: 538px; width: 118px; }
  .quote--three { left: 342px; top: 538px; width: 152px; }
  .quote--four { left: 214px; top: 600px; width: 285px; }
  .quote-rule { top: 538px; width: 1px; height: 46px; background: #aaa; }
  .quote-rule--a { left: 206px; }
  .quote-rule--b { left: 335px; }
</style>
</head>
<body>

<section class="page page--front">
  <div class="abs brand-mark" aria-hidden="true"></div>
  <div class="abs brand-name">Dunfield Inc</div>
  <div class="abs contact-rule"></div>
  <address class="abs contact contact--address" style="font-style:normal">
    1180 Ridge Avenue NW,<br>Calgary Alberta,<br>Canada, T3B 1K9
  </address>
  <div class="abs contact contact--lines">
    <b>P</b>03.555.0142<br><b>F</b>000 000 000<br><b>E</b>martinh@dunfieldinc.ca
  </div>

  <div class="abs hero-panel"></div>
  <h1 class="abs headline">Entrepreneurs helping<br>entrepreneurs,</h1>
  <h2 class="abs subhead">providing strategic financial services</h2>
  <p class="abs intro">By engaging Dunfield Inc, entrepreneurs can regularly access senior executive financial acumen and strategic discipline without having to hire a full-time financial executive or overspend on third-party service providers who are transactional in nature.</p>

  <h3 class="abs tab tab--about">Who we are?</h3>
  <div class="abs body-copy about-copy">
    <p>Dunfield Inc. evolved out of the companies, partnerships and relationships that Martin Halberg, its founder, has nurtured and built over the last 22 years.  Mr. Halberg, the founder of Dunfield, is an entrepreneur himself having built his own companies and managed several successful investment funds whose mandates were to invest in entrepreneurial growth companies.</p>
    <p>Over his career, he has worked extensively with entrepreneurs like himself who have struggled to build an experienced and engaged executive management team.</p>
  </div>
  <div class="abs photo-founder" role="img" aria-label="Portrait photo of the founder in a dark suit"></div>
  <div class="abs caption">Martin Halberg,<small>Founder</small></div>

  <div class="abs services-panel"></div>
  <h3 class="abs tab tab--services">Services</h3>
  <ul class="abs bullet-list services-list services-list--left">
    <li>We work intimately with our clients to determine their corporate and personal objectives</li>
    <li>We evaluate corporate strategies and assist in aligning them with financial ones</li>
    <li>We assist in budgeting, investing, financial forecasting and analysis and asset management</li>
  </ul>
  <ul class="abs bullet-list services-list services-list--right">
    <li>We develop and implement accountability financial systems, processes and reporting</li>
    <li>We manage capital raising efforts, tax structuring issues and corporate transactions including mergers, acquisitions, and the sale of your business</li>
  </ul>

  <div class="abs site-url">www.dunfieldinc.ca</div>
</section>

<section class="page page--back">
  <div class="abs back-panel"></div>
  <div class="abs photo-concept" role="img" aria-label="Photo of a businessman writing business keywords on a glass board"></div>
  <div class="abs body-copy bio-copy">
    <p>Mr. Halberg has a proven track record of developing and implementing strategic corporate policy.  His experience and education is in corporate finance, portfolio management and building businesses and he is a registered Portfolio Manager.  He also has earned an MBA from Lakeshore University (1995) and is a Chartered Financial Analyst (CFA, 1999).</p>
    <p>He applies this competence to evaluating an entrepreneur's vision and corporate strategies and assisting in translating them into higher growth, improved efficiency and higher profitability.  He has extensive experience in public and private, debt and equity capital markets, involving raising, managing and investing capital and completing corporate transactions.   He has evaluated hundreds of corporate business strategies for potential investment.</p>
    <p>Other core skills include financial and tax analysis, working with high-performing investment teams, managing financial and accounting functions, designing and implementing operational and compliance systems.</p>
  </div>

  <div class="abs values-panel"></div>
  <h3 class="abs tab tab--values">Core Values</h3>
  <ul class="abs bullet-list values-list">
    <li>We love working with entrepreneurs because they like adventure.  We understand the high energy, creativity and passion required to take high risks and achieve a corporate vision.</li>
    <li>We like entrepreneurs because they are focused on achievement.  They are "can-do" people who take action.</li>
    <li>We like entrepreneurs because their business relationships are like family. Entrepreneurs are personally invested and value personal relationships with amazing people.</li>
    <li>We like entrepreneurs because they work hard and live well.  Health and wellness is as important as financial success, and most of all having fun is central to the mind set of most successful entrepreneurs.</li>
  </ul>

  <div class="abs testimonials-panel"></div>
  <h3 class="abs tab tab--testimonials">Testimonials</h3>
  <p class="abs quote quote--one">“I need a financial executive who gets the numbers, can think strategically and translate that combined expertise and understanding into forward-looking corporate strategies” powerful</p>
  <div class="abs quote-rule quote-rule--a"></div>
  <p class="abs quote quote--two">“I need a financial executive who understands the inherent makeup of an entrepreneur”</p>
  <div class="abs quote-rule quote-rule--b"></div>
  <p class="abs quote quote--three">“If I could hire my equal in a financial capacity, my executive team would be complete” <span style="margin-left:30px">martin's fave</span></p>
  <p class="abs quote quote--four">“I need help implementing better financial systems and process that can be maintained in a disciplined way”</p>

  <div class="abs site-url">www.dunfieldinc.ca</div>
</section>

</body>
</html>
```